Tavo's Spice Blend Dry Roasted and Freshly Ground Spices to create the Authentic and Aromatic Maur

I need a packaging design for a new company based in Kent called Tavo's Spice Blend. the size of the packaging will be for a 250gm bag.

I would like bright colours so that it can stand out from out the other products on a super market shelf

The packaging must have the list of ingredients on the back;

I.e. Ingredients;
Cumin
Coriander
Dried Red Chili
Cinnamon
Cloves
Cardamon
Black Peppercorn
Rice

Reason: Not enough designed to choose from. Tavo's Spice Blend, Dry Roasted and Freshly Ground Spices to create the Authentic and Aromatic flavour Please also add Turmeric to the ingredient list Thank you Brenna Oakhurst

```html
<!DOCTYPE html>
<html lang="en">
<head>
<meta charset="utf-8">
<title>Tavo's Spice Blend – Packaging</title>
<link href="https://fonts.googleapis.com/css2?family=Lato:wght@400;700;900&display=swap" rel="stylesheet">
<style>
  :root {
    --green-deep: #0d5a2c;
    --green-mid: #1f8a3c;
    --green-bright: #3fae3a;
    --white: #ffffff;
    --spice-dark: #a4561a;
    --spice-mid: #cf8a3a;
    --spice-light: #e7b56e;
    --orange: #e8891a;
    --orange-light: #f4a43a;
    --yellow: #ffd21f;
    --tag-yellow: #e6e84a;
    --foot-text: #cfe7cf;
  }
  * { box-sizing: border-box; margin: 0; padding: 0; }
  html, body { width: 1200px; height: 913px; overflow: hidden; }
  body {
    font-family: "Lato", sans-serif;
    background: linear-gradient(180deg, var(--green-deep) 0%, var(--green-mid) 35%, #cfe9d3 70%, var(--white) 100%);
    position: relative;
  }

  /* Header brand name */
  .brand-header {
    position: absolute; left: 0; right: 0; top: 100px;
    display: flex; justify-content: center; align-items: center; gap: 18px;
  }
  .brand-header .brand-mark { width: 26px; height: 26px; background: var(--white); }
  .brand-header .brand-name { color: var(--white); font-weight: 700; font-size: 54px; line-height: 1; }

  /* Pouch panels */
  .pouch { position: absolute; top: 300px; width: 475px; height: 580px; border-radius: 10px; overflow: hidden; }
  .pouch-back { left: 105px; background: var(--white); }
  .pouch-front { left: 620px; background: linear-gradient(180deg, var(--green-mid), var(--green-deep)); }
  .pouch svg.backdrop { position: absolute; inset: 0; }

  /* Back of pouch */
  .spice-heap {
    position: absolute; left: 30px; top: 175px; width: 440px; height: 300px;
    background: radial-gradient(ellipse at 45% 45%, var(--spice-light), var(--spice-mid) 55%, rgba(207,138,58,0) 75%);
  }
  .spice-sample {
    position: absolute; left: 22px; top: 26px; width: 78px; height: 78px; border-radius: 50%;
    background: radial-gradient(circle, var(--spice-mid), var(--spice-dark));
  }
  .back-copy { position: absolute; left: 22px; top: 118px; width: 135px; font-size: 9px; line-height: 1.35; color: var(--green-mid); }
  .mini-brand {
    position: absolute; left: 235px; top: 218px;
    color: var(--white); font-weight: 700; font-size: 15px;
  }
  .ingredients { position: absolute; left: 235px; top: 248px; color: var(--white); }
  .ingredients h2 { font-size: 18px; font-weight: 700; font-style: italic; margin-bottom: 3px; }
  .ingredients ul { list-style: none; font-size: 13px; line-height: 1.28; }

  /* Front of pouch */
  .front-brand {
    position: absolute; left: 0; right: 0; top: 58px; text-align: center;
    color: var(--white); font-weight: 700; font-size: 30px; line-height: 1;
  }
  .tagline { position: absolute; left: 0; right: 0; top: 148px; text-align: center; color: var(--tag-yellow); font-size: 24px; font-weight: 700; }
  .bowl { position: absolute; border-radius: 50%; border: 6px solid #e6e6e6; background: radial-gradient(circle, var(--spice-light), var(--spice-dark)); }
  .bowl-small { left: 290px; top: 222px; width: 150px; height: 72px; }
  .bowl-large { left: 20px; top: 285px; width: 400px; height: 200px; }
  .flavour-tag {
    position: absolute; left: 280px; top: 275px; padding: 4px 16px;
    background: var(--orange); color: var(--yellow); font-size: 32px; font-weight: 900;
    border-radius: 6px;
  }
  .front-foot { position: absolute; bottom: 22px; left: 28px; right: 28px; display: flex; justify-content: space-between; color: var(--foot-text); font-size: 10px; }
</style>
</head>
<body>

  <header class="brand-header">
    <span class="brand-mark" aria-hidden="true"></span>
    <h1 class="brand-name">Tavo's Spice Blend</h1>
  </header>

  <section class="pouch pouch-back" aria-label="Back of pouch">
    <svg class="backdrop" viewBox="0 0 475 580" width="475" height="580" aria-hidden="true">
      <path d="M180 0 L475 0 L475 150 Q330 70 180 0 Z" fill="#1f8a3c"/>
      <path d="M0 430 Q160 520 280 580 L0 580 Z" fill="#1f8a3c"/>
    </svg>
    <div class="spice-heap" role="img" aria-label="Heap of ground curry spice"></div>
    <div class="spice-sample" role="img" aria-label="Small close-up of ground spice"></div>
    <p class="back-copy">Dry roasted and freshly ground spices for an authentic, aromatic flavour in every spoonful of your favourite curry.</p>
    <div class="mini-brand">Tavo's Spice Blend</div>
    <div class="ingredients">
      <h2>I.e. Ingredients</h2>
      <ul>
        <li>Cumin</li><li>Coriander</li><li>Dried Red Chili</li><li>Cinnamon</li>
        <li>Cloves</li><li>Cardamon</li><li>Black Peppercorn</li><li>Rice</li>
        <li>Turmeric</li>
      </ul>
    </div>
  </section>

  <section class="pouch pouch-front" aria-label="Front of pouch">
    <svg class="backdrop" viewBox="0 0 475 580" width="475" height="580" aria-hidden="true">
      <path d="M0 250 Q240 190 475 215 L475 510 Q240 540 0 500 Z" fill="#e8891a"/>
      <path d="M0 262 Q240 204 475 228 L475 498 Q240 526 0 488 Z" fill="#f4a43a"/>
    </svg>
    <div class="front-brand">Tavo's Spice Blend</div>
    <p class="tagline">Lorem ipsum dolor sit amet</p>
    <div class="bowl bowl-large" role="img" aria-label="Bowl of ground curry spice"></div>
    <div class="bowl bowl-small" role="img" aria-label="Small bowl of ground curry spice"></div>
    <div class="flavour-tag">Original</div>
    <div class="front-foot">
      <span>Produced by Tavo's Spice Blend, Kent</span>
      <span>Net weight 250g</span>
    </div>
  </section>

</body>
</html>
```